I need a flyer made , the flyer can be one page or two pages or three pages . I will be posting this on Instagram and social media platforms. I am a luxury home builder , I am looking to hire a construction project manager . Below are some examples and ideas what can be on the flyer

We’re looking for a construction project manager who’s passionate about building luxury homes at the highest standards
We’re hiring construction project manager
* Experience 5+ years in residential project management with a strong portfolio of completed homes.
* location : Bergen County NJ
* excellent leadership skills, leads teams with confidence and clarity
* communicates seamlessly with architects , engineers, designers and clients
*knows how to manage budgets and timelines without compromising quality
*solves problems with a positive solution first mindset
* pays attention to every detail because in luxury the small things are the big things

Apply now , link in bio or DM to connect.

My logo is attached, my web site www.velstridebuilders.com
My style is modern but still warm and inviting. I like a clean classy look .

Please don’t add any images of chairs or people to the flyer , I do not want people on my flyer. Do not add standard images of offices and houses , we are luxury builders , we build homes over 2 million dollars. Keep a classy , simple modern look . High end .

You can add a white hard hat with my logo on it for a image , this is a suggestion does not have to be on my flyer ,

```html
<!DOCTYPE html>
<html lang="en">
<head>
<meta charset="utf-8">
<title>Velstride Builders — Hiring Flyer</title>
<link rel="stylesheet" href="https://fonts.googleapis.com/css2?family=Bodoni+Moda:wght@500;600&family=Poppins:wght@300;400;500&display=swap">
<style>
  :root {
    --stage: #cdd1d8;
    --night-deep: #1a2230;
    --night-mid: #2a3140;
    --night-warm: #3a3630;
    --ink-light: #ffffff;
    --ink-soft: #e6e8ec;
    --rule: rgba(255,255,255,0.55);
    --rule-faint: rgba(255,255,255,0.35);
    --band-light: #f2f2f2;
    --band-ink: #111111;
  }
  * { margin: 0; padding: 0; box-sizing: border-box; }
  html, body { width: 1200px; height: 692px; overflow: hidden; }
  body { background: var(--stage); position: relative; font-family: "Poppins", sans-serif; color: var(--ink-light); }

  .flyer {
    position: absolute; top: 115px; width: 464px; height: 464px; overflow: hidden;
  }
  .flyer--cover { left: 119px; }
  .flyer--details { left: 596px; }

  .flyer__backdrop {
    position: absolute; inset: 0;
    background:
      radial-gradient(ellipse at 75% 55%, rgba(120,95,60,0.35), transparent 55%),
      linear-gradient(180deg, var(--night-deep) 0%, var(--night-mid) 55%, var(--night-warm) 100%);
  }
  .flyer--details .flyer__backdrop::after {
    content: ""; position: absolute; inset: 0; background: rgba(20,26,38,0.35);
  }
  .flyer__frame {
    position: absolute; left: 17px; top: 17px; right: 17px; bottom: 17px;
    border: 1px solid var(--rule);
  }

  .brand {
    position: absolute; left: 0; right: 0; top: 38px; text-align: center;
    font-family: "Bodoni Moda", serif; font-weight: 500; font-size: 22px;
    letter-spacing: 1.5px; color: var(--ink-light);
  }

  .site-url {
    position: absolute; left: 0; right: 0; top: 429px; text-align: center;
    font-family: "Poppins", sans-serif; font-weight: 300; font-size: 13px;
    letter-spacing: 3.4px; color: var(--ink-soft); opacity: 0.8;
  }

  /* cover */
  .cover-title {
    position: absolute; left: 0; right: 0; text-align: center;
    font-family: "Bodoni Moda", serif; font-weight: 600; line-height: 1;
  }
  .cover-title--small { top: 100px; font-size: 48px; }
  .cover-title--large { top: 142px; font-size: 84px; letter-spacing: -1px; }

  .cover-feature {
    position: absolute; left: 150px; top: 222px; width: 164px; height: 198px;
    background: radial-gradient(ellipse at 50% 90%, rgba(255,255,255,0.35), transparent 60%),
                linear-gradient(180deg, rgba(240,240,240,0.12), rgba(200,200,200,0.05));
    border-radius: 6px;
  }

  /* details */
  .intro {
    position: absolute; left: 20px; right: 20px; top: 88px; text-align: center;
    font-weight: 500; font-size: 12.4px; line-height: 15px;
  }
  .role-title {
    position: absolute; left: 0; right: 0; top: 140px; text-align: center;
    font-weight: 300; font-size: 21px; line-height: 22px; letter-spacing: 0.2px;
  }
  .requirements {
    position: absolute; left: 30px; width: 404px; top: 319px; list-style: none;
  }
  .requirements { top: 203px; }
  .requirements li {
    position: relative; height: 18.5px; padding-left: 14px;
    font-size: 7.9px; line-height: 17px; color: var(--ink-soft);
    border-bottom: 1px solid var(--rule-faint);
    white-space: nowrap;
  }
  .requirements li::before {
    content: ""; position: absolute; left: 0; top: 7px;
    width: 5px; height: 5px; border-radius: 50%; background: var(--ink-light);
  }

  .apply-band {
    position: absolute; left: 48px; width: 368px; top: 371px; height: 29px;
    background: linear-gradient(90deg, rgba(242,242,242,0.25) 0%, var(--band-light) 30%, var(--band-light) 70%, rgba(242,242,242,0.25) 100%);
    text-align: center; color: var(--band-ink);
  }
  .apply-band__headline { display: block; font-weight: 500; font-size: 11px; line-height: 12px; padding-top: 4px; letter-spacing: 0.3px; }
  .apply-band__sub { display: block; font-weight: 400; font-size: 7.6px; line-height: 9px; }
</style>
</head>
<body>

<section class="flyer flyer--cover">
  <div class="flyer__backdrop" role="img" aria-label="Dusk photograph of a modern luxury villa with lit windows and terrace"></div>
  <div class="flyer__frame"></div>
  <div class="brand">VELSTRIDE BUILDERS</div>
  <div class="cover-title cover-title--small">We’re</div>
  <div class="cover-title cover-title--large">Hiring</div>
  <div class="cover-feature" role="img" aria-label="White leather office chair under a soft spotlight"></div>
  <div class="site-url">www.velstridebuilders.com</div>
</section>

<section class="flyer flyer--details">
  <div class="flyer__backdrop" role="img" aria-label="Dimmed dusk photograph of a modern luxury villa"></div>
  <div class="flyer__frame"></div>
  <div class="brand">VELSTRIDE BUILDERS</div>
  <p class="intro">We’re looking for a construction project manager who’s<br>passionate about building luxury homes at the highest standards</p>
  <h1 class="role-title">WE’RE HIRING<br>CONSTRUCTION PROJECT MANAGER</h1>
  <ul class="requirements">
    <li>Experience 5+ years in residential project management with a strong portfolio of completed homes</li>
    <li>Location : Bergen County NJ</li>
    <li>Excellent leadership skills, leads teams with confidence and clarity</li>
    <li>Communicates seamlessly with architects, engineers, designers and clients</li>
    <li>Knows how to manage budgets and timelines without compromising quality</li>
    <li>Solves problems with a positive solution first mindset</li>
    <li>Pays attention to every detail because in luxury the small things are the big things</li>
  </ul>
  <div class="apply-band">
    <span class="apply-band__headline">APPLY NOW,</span>
    <span class="apply-band__sub">LINK IN BIO OR DM TO CONNECT</span>
  </div>
  <div class="site-url">www.velstridebuilders.com</div>
</section>

</body>
</html>
```